Website for "Bright Morrow Ltd" cleaning bsuiness

We require a website to expose our business to the local market. We want to provide background on who we are and what we do but in an easily digestible way. We clean domestic and commercial premises and want to provide a list of all of our services to potential customers. We operate out of Warrington in the UK.

We would like the website to be animated in some way so that the experience of using it is not dull or mundane. This website needs to be an extension of our company.

Target Market(s)

30 - 60 year olds for Domestic plus commercial clients

Industry/Entity Type

Cleaning Service

Coding

Coded - Design and coding required

Number of Pages Required

4 page

Font styles to use
Sans Serif

Colors
0455a3
3176b5
85acd3
cfdeed
ffffff
000000
1b1b1b
c8c8c8
757575

Requirements
Must have
• Logo which has been provided. Theme based around the logo and its colours. Simple layout to avoid confusion.
Nice to have
• Animations where possible to impress the customer.
Should not have
• any pictures of cleaning equipment, fairies, maids etc

```html
<!DOCTYPE html>
<html lang="en">
<head>
<meta charset="utf-8">
<title>Bright Morrow Ltd — Professional Cleaning Services</title>
<link href="https://fonts.googleapis.com/css2?family=Josefin+Sans:wght@300;400;600&family=Roboto:wght@300;400;500;700&family=Great+Vibes&display=swap" rel="stylesheet">
<style>
:root{
  --brand:#0455a3;
  --brand-mid:#3176b5;
  --brand-soft:#85acd3;
  --brand-pale:#cfdeed;
  --white:#ffffff;
  --ink:#1b1b1b;
  --rule:#c8c8c8;
  --muted:#757575;
  --navy:#1d2b44;
  --footer-dark:#13305a;
  --section-grey:#f1f1f1;
  --star:#e8893a;
}
*{box-sizing:border-box;margin:0;padding:0}
html,body{width:1200px;height:2752px;overflow:hidden}
body{position:relative;background:var(--white);font-family:'Roboto',sans-serif;color:var(--ink)}
.abs{position:absolute}

/* header */
.site-header{left:0;top:0;width:1200px;height:127px;background:var(--white)}
.brand{left:100px;top:42px;display:flex;align-items:center;gap:10px}
.brand-dot{width:18px;height:18px;border-radius:50%;background:var(--brand)}
.brand-name{font-family:'Roboto',sans-serif;font-weight:700;font-size:26px;color:var(--brand);letter-spacing:.2px}
.contact-strip{right:99px;top:30px;display:flex;gap:44px;font-size:15px;color:#555}
.contact-strip span{display:flex;align-items:center;gap:10px}
.contact-strip b{color:var(--ink);font-weight:500}
.chip{width:22px;height:20px;border-radius:3px;background:var(--brand-mid);display:flex;align-items:center;justify-content:center}
.main-nav{right:99px;top:77px;display:flex;gap:32px;font-size:13.5px;color:#333;text-transform:uppercase}
.main-nav .active{color:var(--brand-mid)}

/* hero */
.hero{left:0;top:127px;width:1200px;height:543px;background:linear-gradient(120deg,#2a2d33 0%,#4a4e55 35%,#2b2e33 60%,#51565c 100%)}
.hero-frame{left:217px;top:101px;width:765px;height:387px;border:1.5px solid rgba(255,255,255,.35);background:rgba(0,0,0,.18)}
.hero-title{left:0;top:272px;width:1200px;text-align:center;font-family:'Josefin Sans',sans-serif;font-weight:300;font-size:50px;letter-spacing:2px;color:var(--white);animation:rise 1.2s ease-out both}
.hero-rule{left:284px;top:350px;width:633px;height:2px;background:var(--white)}
.hero-sub{left:0;top:365px;width:1200px;text-align:center;font-family:'Great Vibes',cursive;font-size:38px;color:var(--white);animation:rise 1.6s ease-out both}
.hero-arrow{top:228px}
@keyframes rise{from{opacity:0;transform:translateY(16px)}to{opacity:1;transform:none}}

/* section headings */
.section-title{font-family:'Josefin Sans',sans-serif;font-weight:400;font-size:29px;text-transform:uppercase;color:var(--ink)}
.title-bar{width:86px;height:3px;background:var(--brand-mid)}
.body-copy{font-size:11.6px;line-height:23px;color:var(--muted)}

/* about */
.about-title{left:99px;top:722px}
.about-bar{left:99px;top:770px}
.about-copy{left:99px;top:795px;width:534px}
.about-copy p+p{margin-top:12px}
.btn-primary{left:99px;top:1009px;width:118px;height:42px;background:var(--brand);color:var(--white);font-size:12.5px;font-weight:500;text-transform:uppercase;display:flex;align-items:center;justify-content:center;border-radius:3px;box-shadow:0 2px 0 #033d75}
.video-card{left:686px;top:728px;width:415px;height:323px;background:linear-gradient(180deg,#6d5a55 0%,#8a7a70 45%,#c9c1b6 100%)}
.video-bar{left:0;top:0;width:415px;height:50px;background:var(--brand-mid);color:var(--white);font-size:14px;font-weight:500;text-transform:uppercase;display:flex;align-items:center;padding-left:19px}
.video-tools{right:16px;top:16px;display:flex;gap:20px}
.video-play{left:185px;top:153px}

/* services */
.services{left:0;top:1114px;width:1200px;height:495px;background:var(--section-grey)}
.services-title{left:0;top:54px;width:1200px;text-align:center}
.services-bar{left:557px;top:102px}
.service-card{top:139px;width:308px}
.service-photo{width:308px;height:180px}
.service-name{margin-top:24px;font-size:15.5px;font-weight:700;text-transform:uppercase;color:var(--ink)}
.service-copy{margin-top:10px;text-align:justify;font-size:11.6px;line-height:23px;color:var(--muted)}

/* what we do / who we are */
.what-we-do{left:0;top:1609px;width:600px;height:305px;background:var(--brand)}
.panel-title{font-family:'Josefin Sans',sans-serif;font-size:27px;text-transform:uppercase;color:var(--white)}
.panel-bar{width:86px;height:3px;background:var(--white)}
.what-title{left:99px;top:42px}
.what-bar{left:99px;top:84px}
.what-copy{left:99px;top:105px;width:500px;font-size:11.6px;line-height:22px;color:var(--brand-pale)}
.features{left:99px;top:200px;display:flex;gap:0}
.feature{width:160px;text-align:center;font-size:11.6px;font-weight:500;text-transform:uppercase;color:var(--white)}
.feature svg{display:block;margin:0 auto 14px}
.who-we-are{left:0;top:1914px;width:600px;height:194px;background:var(--navy)}
.who-title{left:99px;top:38px}
.who-bar{left:99px;top:80px}
.who-copy{left:99px;top:108px;width:470px;font-size:11.6px;line-height:22px;color:#4b5a74}
.city-photo{left:600px;top:1609px;width:600px;height:499px;background:linear-gradient(180deg,#4d7fbf 0%,#7aa2d4 28%,#2f4a72 55%,#1a2235 80%,#3a2f2c 100%)}

/* testimonials */
.testi-title{left:0;top:2151px;width:1200px;text-align:center;font-size:25px}
.testi-sub{left:0;top:2190px;width:1200px;text-align:center;font-family:'Josefin Sans',sans-serif;font-style:italic;font-size:13px;color:#999}
.testimonial{top:2253px;width:470px;height:120px}
.avatar{left:0;top:0;width:123px;height:114px;border:3px solid var(--white);box-shadow:0 0 0 1px var(--rule)}
.client-name{left:149px;top:6px;font-size:15px;font-weight:500;text-transform:uppercase;color:var(--ink)}
.client-role{left:149px;top:34px;font-size:11px;color:var(--rule)}
.client-role span{color:var(--star);letter-spacing:1px;margin-left:8px}
.client-quote{left:149px;top:58px;width:320px;text-align:justify;font-size:11.6px;line-height:22px;color:var(--muted)}

/* footer */
.site-footer{left:0;top:2428px;width:1200px;height:269px;background:linear-gradient(180deg,#0a4e98,#0455a3)}
.footer-col{top:55px}
.footer-head{font-size:17px;font-weight:700;text-transform:uppercase;color:var(--white);margin-bottom:24px}
.footer-list{list-style:none;font-size:13px;color:var(--white)}
.footer-list li{height:33px;display:flex;align-items:center;gap:14px}
.footer-list .chev{font-size:13px;width:10px}
.social-row{display:flex;gap:7px}
.social-dot{width:36px;height:36px;border:2px solid var(--white);border-radius:50%}
.join-copy{font-size:12px;line-height:24px;color:var(--white);width:200px}
.btn-join{margin-top:12px;width:92px;height:34px;border:1.5px solid var(--white);background:var(--brand-mid);color:var(--white);font-size:12px;display:flex;align-items:center;justify-content:center;border-radius:2px}
.copyright-bar{left:0;top:2697px;width:1200px;height:55px;background:var(--footer-dark);color:var(--white);font-size:12px;display:flex;align-items:center;justify-content:center}
</style>
</head>
<body>

<header class="site-header abs">
  <div class="brand abs"><span class="brand-dot"></span><span class="brand-name">Bright Morrow Ltd</span></div>
  <div class="contact-strip abs">
    <span><i class="chip"><svg width="12" height="12" viewBox="0 0 24 24"><path fill="#fff" d="M6.6 10.8a15 15 0 0 0 6.6 6.6l2.2-2.2c.3-.3.7-.4 1-.2 1.1.4 2.3.6 3.6.6.6 0 1 .4 1 1V20c0 .6-.4 1-1 1A17 17 0 0 1 3 4c0-.6.4-1 1-1h3.5c.6 0 1 .4 1 1 0 1.3.2 2.5.6 3.6.1.3 0 .7-.2 1z"/></svg></i>Call us on <b>5550 1284</b></span>
    <span><i class="chip"><svg width="12" height="10" viewBox="0 0 24 18"><rect x="1" y="1" width="22" height="16" fill="none" stroke="#fff" stroke-width="2.4"/><path d="M1 1l11 9 11-9" fill="none" stroke="#fff" stroke-width="2.4"/></svg></i>Email us on <b>enquiries@brightmorrow.example</b></span>
  </div>
  <nav class="main-nav abs">
    <span class="active">Home</span><span>About Us</span><span>Services</span><span>Who We Are</span><span>Why You Choose</span><span>What We Do</span><span>Contact Us</span>
  </nav>
</header>

<section class="hero abs" role="img" aria-label="Photo of a modern glass-fronted building lobby at dusk">
  <div class="hero-frame abs"></div>
  <h1 class="hero-title abs">BRIGHT MORROW LTD</h1>
  <div class="hero-rule abs"></div>
  <p class="hero-sub abs">Professional Cleaning Services</p>
  <svg class="hero-arrow abs" style="left:48px" width="22" height="84" viewBox="0 0 22 84"><path d="M20 2L2 42l18 40" fill="none" stroke="#fff" stroke-width="2"/></svg>
  <svg class="hero-arrow abs" style="left:1130px" width="22" height="84" viewBox="0 0 22 84"><path d="M2 2l18 40L2 82" fill="none" stroke="#fff" stroke-width="2"/></svg>
</section>

<section class="about">
  <h2 class="section-title about-title abs">About Bright Morrow</h2>
  <div class="title-bar about-bar abs"></div>
  <div class="about-copy body-copy abs">
    <p>It is a long established fact that a reader will be distracted by the readable content of a page when looking at its layout. The point of using Lorem Ipsum is that it has a more-or-less normal distribution of letters, as opposed to using 'Content here, content here', making it look like readable English. Many desktop publishing packages and web page editors now use that it has a more-or-less</p>
    <p>Lorem Ipsum as their default model text, and a search for 'lorem ipsum' will uncover many web sites still in their infancy. Various versions have evolved over the years, sometimes by accident, sometimes on purpose (injected humour and the like) search for 'lorem ipsum' will uncover</p>
  </div>
  <a class="btn-primary abs">Learn More</a>
  <div class="video-card abs" role="img" aria-label="Video still of a tidy living room with a sofa and tall windows">
    <div class="video-bar abs">Cleaning Services Company</div>
    <div class="video-tools abs">
      <svg width="18" height="16" viewBox="0 0 18 16"><path d="M10 1l7 6-7 6V9C5 9 2 11 1 15 1 9 4 5 10 5z" fill="#fff"/></svg>
      <svg width="16" height="16" viewBox="0 0 16 16"><path d="M1 1h5M1 1v5M1 1l5 5M15 1h-5M15 1v5M15 1l-5 5M1 15h5M1 15v-5M1 15l5-5M15 15h-5M15 15v-5M15 15l-5-5" stroke="#fff" stroke-width="2" fill="none"/></svg>
    </div>
    <svg class="video-play abs" width="46" height="46" viewBox="0 0 46 46"><circle cx="23" cy="23" r="21" fill="rgba(0,0,0,.25)" stroke="#fff" stroke-width="2"/><path d="M18 14l14 9-14 9z" fill="#fff"/></svg>
  </div>
</section>

<section class="services abs">
  <h2 class="section-title services-title abs">Our Best Services</h2>
  <div class="title-bar services-bar abs"></div>
  <article class="service-card abs" style="left:97px">
    <div class="service-photo" role="img" aria-label="Glass office tower seen from below against a bright sky" style="background:linear-gradient(135deg,#e9d9b0 0%,#6fa2c9 35%,#1f5a86 70%,#0f2f4d 100%)"></div>
    <h3 class="service-name">Commercial Premises</h3>
    <p class="service-copy">Contrary to popular belief, Lorem Ipsum is not simply random text. It has roots in a piece of classical Latin litera ture from 45 BC, making it over years old.</p>
  </article>
  <article class="service-card abs" style="left:446px">
    <div class="service-photo" role="img" aria-label="Bright family living room with white sofas and a fireplace" style="background:linear-gradient(180deg,#d9d2c6 0%,#b9a48b 45%,#8b6e52 75%,#e8e2d8 100%)"></div>
    <h3 class="service-name">Domestic Premises</h3>
    <p class="service-copy">Contrary to popular belief, Lorem Ipsum is not simply random text. It has roots in a piece of classical Latin litera ture from 45 BC, making it over years old.</p>
  </article>
  <article class="service-card abs" style="left:795px">
    <div class="service-photo" role="img" aria-label="Clean office corridor with blue glass walls and an orange doorway" style="background:linear-gradient(90deg,#8fb6dd 0%,#5b8ec4 30%,#c8552c 50%,#5b8ec4 70%,#b9d2ea 100%)"></div>
    <h3 class="service-name">Commercial Premises</h3>
    <p class="service-copy">Contrary to popular belief, Lorem Ipsum is not simply random text. It has roots in a piece of classical Latin litera ture from 45 BC, making it over years old.</p>
  </article>
</section>

<section class="what-we-do abs">
  <h2 class="panel-title what-title abs">What We Do</h2>
  <div class="panel-bar what-bar abs"></div>
  <p class="what-copy abs">Established in 2004, Ashdown Logistics is proud of its history and the role played in the economic development of the local marketplace. This success has given us the confidence to expand our service offering and reach into North American markets.</p>
  <div class="features abs">
    <div class="feature"><svg width="26" height="26" viewBox="0 0 24 24"><path fill="#fff" d="M19.4 13a7.5 7.5 0 0 0 0-2l2.1-1.6-2-3.5-2.5 1a7 7 0 0 0-1.7-1L15 3h-4l-.4 2.9a7 7 0 0 0-1.7 1l-2.5-1-2 3.5L6.6 11a7.5 7.5 0 0 0 0 2l-2.1 1.6 2 3.5 2.5-1a7 7 0 0 0 1.7 1L11 21h4l.4-2.9a7 7 0 0 0 1.7-1l2.5 1 2-3.5zM13 15.5a3.5 3.5 0 1 1 0-7 3.5 3.5 0 0 1 0 7z"/></svg>Unlimited Services</div>
    <div class="feature"><svg width="26" height="26" viewBox="0 0 24 24"><path fill="#fff" d="M6.6 10.8a15 15 0 0 0 6.6 6.6l2.2-2.2c.3-.3.7-.4 1-.2 1.1.4 2.3.6 3.6.6.6 0 1 .4 1 1V20c0 .6-.4 1-1 1A17 17 0 0 1 3 4c0-.6.4-1 1-1h3.5c.6 0 1 .4 1 1 0 1.3.2 2.5.6 3.6.1.3 0 .7-.2 1z"/></svg>All Our Supports</div>
    <div class="feature"><svg width="26" height="26" viewBox="0 0 24 24"><circle cx="12" cy="7" r="5" fill="#fff"/><path fill="#fff" d="M2 23c0-6 4.5-9 10-9s10 3 10 9z"/></svg>100% Responsabel</div>
  </div>
</section>

<section class="who-we-are abs">
  <h2 class="panel-title who-title abs">Who We Are</h2>
  <div class="panel-bar who-bar abs"></div>
  <p class="who-copy abs">Providing global transportation solutions to our clients through consultative analysis that engage all stakeholders and encourage process development.</p>
</section>

<div class="city-photo abs" role="img" aria-label="City skyline of glass towers at dusk with light trails on a curving highway"></div>

<section class="testimonials">
  <h2 class="section-title testi-title abs">Our Client Testimonial</h2>
  <p class="testi-sub abs">What Our Client Says About us</p>
  <article class="testimonial abs" style="left:97px">
    <div class="avatar abs" role="img" aria-label="Portrait photo of the client" style="background:linear-gradient(160deg,#a88a70,#5e4636)"></div>
    <h3 class="client-name abs">Callum R.</h3>
    <p class="client-role abs">Customers<span>★★★★★</span></p>
    <p class="client-quote abs">Martin is a very innovative designer. He is very prompt with his responses and I have absolutely no complaints related to customer service or the results of his products.</p>
  </article>
  <article class="testimonial abs" style="left:637px">
    <div class="avatar abs" role="img" aria-label="Portrait photo of the client" style="background:linear-gradient(160deg,#e2d5c4,#b9a189)"></div>
    <h3 class="client-name abs">Priya S.</h3>
    <p class="client-role abs">Customers<span>★★★★★</span></p>
    <p class="client-quote abs">Martin is the kind of person would like to deal with. A thorough dedicated professional who is prompt and courteous. His indicators are not only accurate</p>
  </article>
</section>

<footer class="site-footer abs">
  <div class="footer-col abs" style="left:99px">
    <h4 class="footer-head">Get In Touch</h4>
    <ul class="footer-list">
      <li><svg width="12" height="12" viewBox="0 0 24 24"><path fill="#fff" d="M6.6 10.8a15 15 0 0 0 6.6 6.6l2.2-2.2c.3-.3.7-.4 1-.2 1.1.4 2.3.6 3.6.6.6 0 1 .4 1 1V20c0 .6-.4 1-1 1A17 17 0 0 1 3 4c0-.6.4-1 1-1h3.5c.6 0 1 .4 1 1 0 1.3.2 2.5.6 3.6.1.3 0 .7-.2 1z"/></svg>Phone: 01925 555 014</li>
      <li><svg width="12" height="12" viewBox="0 0 24 24"><rect x="2" y="8" width="20" height="12" fill="#fff"/><rect x="6" y="2" width="12" height="6" fill="#fff"/></svg>Fax: 01925 555 027</li>
      <li><svg width="12" height="10" viewBox="0 0 24 18"><rect x="1" y="1" width="22" height="16" fill="none" stroke="#fff" stroke-width="2.4"/><path d="M1 1l11 9 11-9" fill="none" stroke="#fff" stroke-width="2.4"/></svg>Email: sales@brightmorrow.co.uk</li>
      <li><svg width="12" height="12" viewBox="0 0 24 24"><circle cx="12" cy="12" r="10" fill="#fff"/></svg>Web: www.brightmorrow.co.uk</li>
    </ul>
  </div>
  <div class="footer-col abs" style="left:393px">
    <h4 class="footer-head">Quick Links</h4>
    <ul class="footer-list">
      <li><span class="chev">»</span>About Us</li>
      <li><span class="chev">»</span>Services</li>
      <li><span class="chev">»</span>Testimonial</li>
      <li><span class="chev">»</span>News &amp; Media</li>
    </ul>
  </div>
  <div class="footer-col abs" style="left:615px">
    <h4 class="footer-head">Social Media</h4>
    <div class="social-row"><span class="social-dot"></span><span class="social-dot"></span><span class="social-dot"></span><span class="social-dot"></span><span class="social-dot"></span></div>
  </div>
  <div class="footer-col abs" style="left:917px">
    <h4 class="footer-head">Join Us</h4>
    <p class="join-copy">Share, edit and publish documents in a unified system, improve</p>
    <a class="btn-join">Join Us Now</a>
  </div>
</footer>
<div class="copyright-bar abs">Copyrights@2016Company Name , All rights Reserved</div>

</body>
</html>
```